WordPress website design for wealth management company

A modern clean look website for a service company. This is mostly for information only, with a form to capture prospect contact information and schedule a 15 minutes call. There will be several static pages describe what services we offer, how we are different, and a blog section for posting articles and share resources. A section for client testimonials.
I want a website that is easy to understand and maintain. No proprietary plugins that cost extra. The main thing I need help is the visual layout / color palette that present a clean and professional look, select the suitable stock photos that convey the image of trust, professional, innovative, and high service.
Some websites with style I like include the following
- https://www.halvorbrook.com/
- https://www.trivanplanningworks.com/
- https://morvellfunds.com/private-equity-partners/
Also some websites in other industries with clean modern look
- https://zentrell.com/
- https://quovra.com/
- https://www.plumtorvik.com/
I want the end product to be a fully functional website that I can upload into web hosting service I use and I can easily add content and maintain myself in the future.

```html
<!DOCTYPE html>
<html lang="en">
<head>
<meta charset="utf-8">
<title>Marrowby Wealth</title>
<link rel="stylesheet" href="https://fonts.googleapis.com/css2?family=Playfair+Display:wght@400;500;600;700&family=Mulish:wght@400;500;600;700;800&display=swap">
<style>
:root{
  --purple:#521f7c;
  --purple-deep:#4a1a72;
  --purple-line:#8a63ad;
  --yellow:#fbb62c;
  --ink:#2b2233;
  --muted:#5a5360;
  --lavender:#f8f4fb;
  --white:#ffffff;
  --serif:'Playfair Display', serif;
  --sans:'Mulish', sans-serif;
}
*{box-sizing:border-box;margin:0;padding:0}
html,body{width:1200px;height:3949px;overflow:hidden}
body{font-family:var(--sans);color:var(--ink);background:var(--white);position:relative}
section,header,footer{position:relative;width:1200px;overflow:hidden}
.abs{position:absolute}
.btn{position:absolute;display:flex;align-items:center;justify-content:center;background:var(--yellow);color:var(--ink);font-family:var(--sans);font-weight:700;font-size:11px;letter-spacing:.3px;border-radius:8px;text-transform:uppercase}
.photo{position:absolute;border-radius:12px}

/* header */
.site-header{height:98px;background:var(--white)}
.brand{position:absolute;left:132px;top:30px;display:flex;align-items:center;gap:10px;color:var(--purple);font-weight:800;font-size:16px;letter-spacing:1px;text-transform:uppercase}
.brand-dot{width:30px;height:30px;border-radius:50%;background:var(--purple)}
.nav a{position:absolute;top:40px;font-size:13px;color:var(--ink);text-decoration:none;letter-spacing:.3px}
.nav a.active{color:var(--purple)}
.nav a.active::after{content:"";position:absolute;left:0;right:0;top:24px;height:2px;background:var(--purple)}

/* hero */
.hero{height:564px;background:linear-gradient(100deg,#c9b9a6 0%,#a9a9a3 30%,#8a9aa0 55%,#b3aba0 75%,#c7b49b 100%)}
.hero-title{position:absolute;left:132px;top:44px;width:440px;font-family:var(--serif);font-weight:700;font-size:32px;line-height:38px;color:var(--white)}
.field{position:absolute;background:var(--white);border-radius:6px;font-size:11px;color:var(--muted);padding:11px 14px}

/* services */
.services{height:603px}
.sec-title{font-family:var(--serif);font-weight:500;color:var(--purple)}
.rule{position:absolute;height:3px;background:var(--yellow)}
.chip{position:absolute;height:41px;display:flex;align-items:center;gap:10px;padding:0 12px;background:var(--white);border-radius:6px;box-shadow:0 2px 10px rgba(60,20,90,.12);font-family:var(--serif);font-weight:600;font-size:12.5px;color:var(--purple);white-space:nowrap}
.chip svg{flex:none}

/* different */
.different{height:558px;background:var(--purple)}
.body-text{font-size:13.5px;line-height:22.5px}
.accent-area{position:absolute}

/* blog */
.blog{height:694px}
.card{position:absolute;top:152px;width:296px;height:440px;background:var(--white);border-radius:8px;box-shadow:0 4px 18px rgba(60,20,90,.12);overflow:hidden}
.card.faded{opacity:.3}
.card h3{position:absolute;left:26px;top:20px;width:240px;font-family:var(--serif);font-weight:600;font-size:17px;line-height:23.5px;color:var(--purple)}
.card .thumb{position:absolute;left:0;top:109px;width:100%;height:166px}
.card p{position:absolute;left:26px;right:22px;top:294px;font-size:12px;line-height:18px;color:var(--muted)}
.card .btn{left:26px;top:386px;width:88px;height:28px;font-size:10px;border-radius:7px}
.dot{position:absolute;top:630px;width:8px;height:8px;border-radius:50%;background:var(--purple)}

/* stats */
.stats{height:207px;background:var(--lavender)}
.stat-num{position:absolute;top:62px;font-family:var(--serif);font-size:42px;color:var(--purple);line-height:1}
.stat-label{position:absolute;top:124px;font-size:15px;color:var(--ink)}
.vline{position:absolute;top:40px;width:1px;height:126px;background:#d8cfe0}

/* testimonials */
.testimonials{height:521px}
.quote-card{position:absolute;top:161px;width:453px;height:288px;background:var(--white);box-shadow:0 4px 18px rgba(60,20,90,.12);border-radius:6px}
.quote-mark{position:absolute;left:-6px;top:-34px;font-family:var(--serif);font-weight:700;font-size:110px;color:var(--purple);line-height:1}
.quote-card p{position:absolute;left:63px;top:46px;width:352px;font-size:13.5px;line-height:23px;color:var(--muted)}
.quote-card hr{position:absolute;left:63px;top:203px;width:352px;border:0;height:1px;background:var(--purple-line)}
.avatar{position:absolute;left:23px;top:224px;width:40px;height:40px;border-radius:50%;background:linear-gradient(#c9c2bb,#8d8079)}
.who{position:absolute;left:73px;top:228px;font-size:13.5px;line-height:22px;color:var(--ink)}

/* cta */
.cta{height:422px;background:var(--yellow);text-align:center}
.cta h2{position:absolute;left:0;right:0;top:56px;font-family:var(--serif);font-weight:500;font-size:32px;line-height:45px;color:var(--ink)}
.cta p{position:absolute;left:0;right:0;top:162px;font-size:17px;line-height:29px;color:var(--ink)}

/* footer */
.site-footer{height:282px;background:var(--purple-deep);color:var(--white)}
.foot-brand{position:absolute;left:119px;top:18px;width:200px;text-align:center;font-weight:700;font-size:22px;line-height:26px;letter-spacing:2px;text-transform:uppercase}
.foot-brand .ring{width:70px;height:70px;border-radius:50%;border:4px solid var(--white);margin:0 auto 12px}
.foot-label{position:absolute;font-family:var(--serif);font-size:18px;font-weight:500}
.foot-value{position:absolute;font-family:var(--serif);font-size:17px}
.foot-menu a{position:absolute;left:716px;font-size:13px;color:var(--white);text-decoration:none}
.social a{position:absolute;left:878px;font-size:13px;color:var(--white);text-decoration:none}
</style>
</head>
<body>

<header class="site-header">
  <div class="brand"><span class="brand-dot"></span>Marrowby Wealth</div>
  <nav class="nav">
    <a class="active" href="#" style="left:374px">HOME</a>
    <a href="#" style="left:448px">ABOUT US</a>
    <a href="#" style="left:550px">SERVICES</a>
    <a href="#" style="left:651px">BLOG</a>
    <a href="#" style="left:720px">CONTACT US</a>
  </nav>
  <div class="btn" style="left:837px;top:26px;width:230px;height:44px">Schedule a 15 minutes call</div>
</header>

<section class="hero" role="img" aria-label="Smiling senior couple holding hands running along the shoreline at sunset">
  <h1 class="hero-title">You, along with your wealth, have the potential to achieve so much more.</h1>
  <div class="field" style="left:132px;top:185px;width:195px;height:36px">First Name</div>
  <div class="field" style="left:339px;top:185px;width:196px;height:36px">Last Name</div>
  <div class="field" style="left:132px;top:232px;width:195px;height:36px">Email id</div>
  <div class="field" style="left:339px;top:232px;width:196px;height:36px">Phone</div>
  <div class="field" style="left:132px;top:279px;width:403px;height:36px">Subject</div>
  <div class="field" style="left:132px;top:328px;width:403px;height:97px">Message</div>
  <div class="btn" style="left:132px;top:443px;width:403px;height:49px;font-size:13px">Schedule a 15 minutes call</div>
</section>

<section class="services">
  <div class="photo" style="left:132px;top:54px;width:417px;height:489px;background:linear-gradient(#e6e4df,#aeb0a5 45%,#7c7650 80%,#6b5a35)" role="img" aria-label="Senior couple hiking on a misty autumn hillside"></div>
  <h2 class="sec-title abs" style="left:599px;top:44px;font-size:33px">Services we offer</h2>
  <div class="rule" style="left:599px;top:94px;width:115px"></div>
  <p class="abs" style="left:599px;top:122px;width:462px;font-size:14px;line-height:22px;color:var(--muted)">Lorem ipsum dolor sit amet, consectetur adipiscing elit, sed do eiusmod tempor incididunt ut labore et dolore magna aliqua. Ut enim ad minim veniam, quis nostrud exercitation.</p>

  <div class="chip" style="left:605px;top:216px;width:198px"><svg width="22" height="22" viewBox="0 0 22 22" fill="none" stroke="#521f7c" stroke-width="1.4"><rect x="4" y="3" width="14" height="16" rx="1"/><path d="M7 8h8M7 12h8M7 16h5"/></svg>Financial Planning</div>
  <div class="chip" style="left:605px;top:270px;width:198px"><svg width="22" height="22" viewBox="0 0 22 22" fill="none" stroke="#521f7c" stroke-width="1.4"><circle cx="8" cy="6" r="3"/><path d="M5 20v-7l3-3 3 3v7M12 16h6"/></svg>Retirement Planning</div>
  <div class="chip" style="left:605px;top:324px;width:198px"><svg width="22" height="22" viewBox="0 0 22 22" fill="none" stroke="#521f7c" stroke-width="1.4"><rect x="4" y="3" width="14" height="16" rx="1"/><path d="M7 7h8M7 10h8M7 13h8M7 16h8"/></svg>Estate Planning</div>
  <div class="chip" style="left:605px;top:378px;width:221px"><svg width="22" height="22" viewBox="0 0 22 22" fill="none" stroke="#521f7c" stroke-width="1.4"><circle cx="12" cy="7" r="4"/><path d="M3 17l5-3h6l4 2M3 20h15"/></svg>Investment Management</div>
  <div class="chip" style="left:605px;top:432px;width:198px"><svg width="22" height="22" viewBox="0 0 22 22" fill="none" stroke="#521f7c" stroke-width="1.4"><rect x="4" y="3" width="14" height="16" rx="1"/><path d="M7 8h8M7 12h4M13 12h2M7 16h8"/></svg>Tax Planning</div>

  <div class="chip" style="left:865px;top:216px;width:199px"><svg width="22" height="22" viewBox="0 0 22 22" fill="none" stroke="#521f7c" stroke-width="1.4"><path d="M2 11l5-4 4 3 4-3 5 4-6 5-3-2-3 2z"/></svg>Business Ownership</div>
  <div class="chip" style="left:865px;top:270px;width:199px"><svg width="22" height="22" viewBox="0 0 22 22" fill="none" stroke="#521f7c" stroke-width="1.4"><circle cx="11" cy="7" r="4"/><path d="M4 20c0-5 3-7 7-7s7 2 7 7"/></svg>Private Client Services</div>
  <div class="chip" style="left:865px;top:324px;width:199px"><svg width="22" height="22" viewBox="0 0 22 22" fill="none" stroke="#521f7c" stroke-width="1.4"><rect x="3" y="3" width="16" height="16" rx="2"/><path d="M7 11l3 3 5-6"/></svg>Insurance</div>
  <div class="chip" style="left:865px;top:378px;width:199px"><svg width="22" height="22" viewBox="0 0 22 22" fill="none" stroke="#521f7c" stroke-width="1.4"><rect x="3" y="6" width="16" height="13" rx="1"/><path d="M8 6V3h6v3M3 11h16"/></svg>Education Savings</div>

  <div class="btn" style="left:605px;top:508px;width:151px;height:35px;font-size:11px">View all services</div>
</section>

<section class="different">
  <div class="accent-area" style="left:835px;top:300px;width:365px;height:258px;background:linear-gradient(135deg,rgba(251,182,44,0) 40%,rgba(251,182,44,.35) 100%)" role="img" aria-label="Decorative diagonal accent in brand yellow"></div>
  <h2 class="abs" style="left:126px;top:70px;font-family:var(--serif);font-weight:500;font-size:32px;color:var(--white)">How we are different</h2>
  <div class="rule" style="left:126px;top:124px;width:114px"></div>
  <p class="abs body-text" style="left:126px;top:162px;width:330px;color:var(--white)">Lorem ipsum dolor sit amet, consectetur adipiscing elit, sed do eiusmod tempor incididunt ut labore et dolore magna aliqua. Ut enim ad minim veniam, quis nostrud exercitation. Sed ut perspiciatis unde omnis iste natus error sit voluptatem accusantium doloremque laudantium, totam rem aperiam, eaque ipsa quae ab illo inventore veritatis et quasi architecto beatae vitae dicta sunt explicabo. Nemo enim ipsam voluptatem quia voluptas sit aspernatur aut odit aut fugit, sed quia consequuntur magni</p>
  <div class="btn" style="left:126px;top:437px;width:101px;height:35px">Read more</div>
  <div class="photo" style="left:501px;top:49px;width:319px;height:454px;background:linear-gradient(150deg,#cfd3d8,#9aa5b0 50%,#5f6e7f)" role="img" aria-label="Advisor's hands with pen beside stacked coins and a calculator"></div>
  <div class="photo" style="left:851px;top:43px;width:219px;height:314px;background:linear-gradient(#c9d3dc,#a9b5bd 45%,#cdb896)" role="img" aria-label="Senior couple walking hand in hand on a beach"></div>
</section>

<section class="blog">
  <h2 class="sec-title abs" style="left:0;right:0;top:46px;text-align:center;font-size:32px">Latest Blog</h2>

  <article class="card faded" style="left:-235px">
    <h3>At vero eos et accusamus et iusto odio dignissimos ducimus</h3>
    <div class="thumb" style="background:linear-gradient(#efe6d6,#c9b995)" role="img" aria-label="Hands holding a small tree"></div>
    <p>Lorem ipsum dolor sit amet, consectetur adipiscing elit, sed do eiusmod tempor incidi dunt ut labore et dolore magna aliqua. Ut enim ad minim.</p>
  </article>

  <article class="card" style="left:132px">
    <h3>At vero eos et accusamus et iusto odio dignissimos ducimus</h3>
    <div class="thumb" style="background:linear-gradient(#f6f3ee,#e3dac6 60%,#b99d5c)" role="img" aria-label="Hands holding a small golden tree"></div>
    <p>Lorem ipsum dolor sit amet, consectetur adipiscing elit, sed do eiusmod tempor incidi dunt ut labore et dolore magna aliqua. Ut enim ad minim.</p>
    <div class="btn">Read more</div>
  </article>

  <article class="card" style="left:453px">
    <h3>At vero eos et accusamus et iusto odio dignissimos ducimus</h3>
    <div class="thumb" style="background:linear-gradient(#eeeae4,#c8b7a0 60%,#8d6a48)" role="img" aria-label="Wooden letter blocks beside rising stacks of coins"></div>
    <p>Lorem ipsum dolor sit amet, consectetur adipiscing elit, sed do eiusmod tempor incidi dunt ut labore et dolore magna aliqua. Ut enim ad minim.</p>
    <div class="btn">Read more</div>
  </article>

  <article class="card" style="left:774px">
    <h3>At vero eos et accusamus et iusto odio dignissimos ducimus</h3>
    <div class="thumb" style="background:linear-gradient(#f0c98c,#a9b9c3 50%,#6f8fa3)" role="img" aria-label="Couple standing on a beach at sunset"></div>
    <p>Lorem ipsum dolor sit amet, consectetur adipiscing elit, sed do eiusmod tempor incidi dunt ut labore et dolore magna aliqua. Ut enim ad minim.</p>
    <div class="btn">Read more</div>
  </article>

  <article class="card faded" style="left:1093px">
    <h3>At vero eos et accusamus et iusto odio dignissimos ducimus</h3>
    <div class="thumb" style="background:linear-gradient(#f0c98c,#c9b49a)" role="img" aria-label="Beach at sunset"></div>
    <p>Lorem ipsum dolor sit amet, consectetur adipiscing elit, sed do eiusmod tempor incidi dunt ut labore et dolore magna aliqua. Ut enim ad minim.</p>
    <div class="btn">Read more</div>
  </article>

  <span class="dot" style="left:569px"></span>
  <span class="dot" style="left:588px;background:var(--yellow)"></span>
  <span class="dot" style="left:607px"></span>
  <span class="dot" style="left:626px"></span>
</section>

<section class="stats">
  <div class="stat-num" style="left:132px">100+</div>
  <div class="stat-label" style="left:132px">Team Members</div>
  <div class="vline" style="left:349px"></div>
  <div class="stat-num" style="left:0;width:1200px;text-align:center">75%</div>
  <div class="stat-label" style="left:0;width:1200px;text-align:center">Clients &amp; Families / Employee Owned</div>
  <div class="vline" style="left:842px"></div>
  <div class="stat-num" style="right:155px;width:200px;text-align:right">19</div>
  <div class="stat-label" style="right:133px">Offices Nationwide</div>
</section>

<section class="testimonials">
  <h2 class="sec-title abs" style="left:0;right:0;top:44px;text-align:center;font-size:32px">Testimonials</h2>
  <div class="rule" style="left:577px;top:103px;width:46px"></div>

  <svg class="abs" style="left:60px;top:288px" width="20" height="24" viewBox="0 0 20 24" fill="none" stroke="#521f7c" stroke-width="1.6"><path d="M17 2L3 12l14 10z"/></svg>
  <svg class="abs" style="left:1106px;top:288px" width="20" height="24" viewBox="0 0 20 24" fill="none" stroke="#521f7c" stroke-width="1.6"><path d="M3 2l14 10L3 22z"/></svg>

  <div class="quote-card" style="left:132px">
    <div class="quote-mark">“</div>
    <p>At vero eos et accusamus et iusto odio dignissimos ducimus qui blanditiis praesentium voluptatum deleniti atque corrupti quos dolores et quas molestias exce pturi sint occaecati cupiditate non provident, similique sunt in culpa qui officia deserunt mollitia animi, id est laborum et dolorum fuga.</p>
    <hr>
    <div class="avatar" role="img" aria-label="Client portrait"></div>
    <div class="who">THOMAS<br>Miami</div>
  </div>

  <div class="quote-card" style="left:615px">
    <div class="quote-mark">“</div>
    <p>At vero eos et accusamus et iusto odio dignissimos ducimus qui blanditiis praesentium voluptatum deleniti atque corrupti quos dolores et quas molestias exce pturi sint occaecati cupiditate non provident, similique sunt in culpa qui officia deserunt mollitia animi, id est laborum et dolorum fuga.</p>
    <hr>
    <div class="avatar" role="img" aria-label="Client portrait"></div>
    <div class="who">THOMAS<br>Miami</div>
  </div>
</section>

<section class="cta">
  <div class="accent-area" style="left:0;top:250px;width:330px;height:172px;background:linear-gradient(45deg,rgba(82,31,124,.35) 0%,rgba(82,31,124,0) 60%)" role="img" aria-label="Decorative diagonal accent in brand purple"></div>
  <h2>Ensure you establish your family office<br>before making your next move.</h2>
  <p>Sed ut perspiciatis unde omnis iste natus error sit voluptatem accusantium doloremque<br>laudantium, totam rem aperiam, eaque ipsa quae ab illo inventore</p>
  <div class="btn" style="left:484px;top:253px;width:232px;height:44px;background:var(--purple);color:var(--white);font-weight:600;font-size:12px">Schedule a 15 minutes call</div>
</section>

<footer class="site-footer">
  <div class="foot-brand"><div class="ring"></div>Marrowby<br>Wealth</div>
  <div class="abs" style="left:349px;top:12px;width:1px;height:138px;background:rgba(255,255,255,.6)"></div>

  <svg class="abs" style="left:398px;top:36px" width="32" height="32" viewBox="0 0 24 24" fill="#ffffff"><path d="M6.6 10.8a15.1 15.1 0 006.6 6.6l2.2-2.2a1 1 0 011-.25 11.4 11.4 0 003.6.57 1 1 0 011 1V20a1 1 0 01-1 1A17 17 0 013 4a1 1 0 011-1h3.5a1 1 0 011 1 11.4 11.4 0 00.57 3.6 1 1 0 01-.25 1z"/></svg>
  <div class="foot-label" style="left:455px;top:22px">Call Us</div>
  <div class="foot-value" style="left:455px;top:47px">+1 555 555 555</div>

  <svg class="abs" style="left:396px;top:108px" width="34" height="26" viewBox="0 0 34 26" fill="none" stroke="#ffffff" stroke-width="2"><rect x="1" y="1" width="32" height="24"/><path d="M1 1l16 13L33 1"/></svg>
  <div class="foot-label" style="left:455px;top:98px">Email Us</div>
  <div class="foot-value" style="left:455px;top:123px">info@marrowby.com</div>

  <div class="foot-label" style="left:716px;top:18px">Menu</div>
  <nav class="foot-menu">
    <a href="#" style="top:53px">Home</a>
    <a href="#" style="top:72px">About Us</a>
    <a href="#" style="top:91px">Services</a>
    <a href="#" style="top:110px">Blog</a>
    <a href="#" style="top:129px">Contact us</a>
  </nav>

  <div class="foot-label" style="left:878px;top:18px">Follow us</div>
  <nav class="social">
    <a href="#" style="top:53px">Photos</a>
    <a href="#" style="top:72px">Community</a>
    <a href="#" style="top:91px">Videos</a>
    <a href="#" style="top:110px">Careers</a>
  </nav>

  <div class="abs" style="left:132px;top:193px;width:936px;height:1px;background:rgba(255,255,255,.7)"></div>
  <div class="abs" style="left:0;right:0;top:234px;text-align:center;font-size:12.5px">Copyright © 2023 All Rights Reserved</div>
</footer>

</body>
</html>
```